Webpage - LORAVEN.COM (Webpage)

Design webpage for LoRaven.com (already own the domain).
At a minimum the webpage should include links and information about:
1. BRAND - https://amberwoodliving.example/
2. SONGS – link to artist and all released songs (3 currently available under Lora Venn on Spotify and other platforms). Ability to add songs as they are released.
3. PODCAST - Links to existing (2) and upcoming podcasts "Days Run Golden" (currently available on Spotify, YouTube and other platforms). Ability to add links to future podcasts.
https://video.example/watch?v=Q-3KtHbWr8Za
4. VOICE COACH - Information about voice coaching/lessons by Lora Venn as well as how to contact regarding the lessons. Ability to add testimonials. Add "click here" link for requesting more information regarding voice lessons, with fields like name, email, cell phone and best method, time to contact that user can fill to request info
5. SOCIAL MEDIA -Links to Lora Venn's Instagram, Facebook, TikTok, YouTube Channel (not yet created), etc.
6. BAND - Link to access information about band “Lora Venn and KOBALTT
https://social.example/kobalttband/?next=%2Fmirelotsan%2Ffeed%2F&locale=en_US%2Cen_US. Add "click here" link for requesting more information regarding voice lessons, with fields like name, email, cell phone and best method, time to contact that user can fill to request info
7. VIDEOS – links to music and promotional videos from solo artist and band. All will eventually be compiled on YouTube channel.
Pictures are included for reference and use but not necessarily asking that they all be on the website. Designer can use discretion from uploaded files or request more if desired.

Coding

Coded - Design and coding required

Number of Pages Required

1 page

Requirements
Must have
• Original artist song plays when opening page. Preferably Hold the Quiet Near or HQN.
Nice to have
• Rotating songs play when clicking any link

```html
<!DOCTYPE html>
<html lang="en">
<head>
<meta charset="utf-8">
<title>Lora Venn — Official Site</title>
<link href="https://fonts.googleapis.com/css2?family=Oswald:wght@400;500;600;700&family=Poppins:wght@400;500;600&display=swap" rel="stylesheet">
<style>
:root{
  --red:#e8322c;
  --yellow:#ffe01b;
  --black:#050505;
  --ink:#1a1a1a;
  --grey:#555;
  --white:#fff;
  --head:'Oswald', sans-serif;
  --body:'Poppins', sans-serif;
}
*{margin:0;padding:0;box-sizing:border-box}
html,body{width:1200px;height:4000px;overflow:hidden}
body{position:relative;background:var(--white);font-family:var(--body);color:var(--ink)}
.abs{position:absolute}
.heading{font-family:var(--head);font-weight:600;text-transform:uppercase;letter-spacing:.5px}

/* header */
.site-header{position:absolute;left:0;top:0;width:1200px;height:124px;background:var(--white);z-index:5}
.wordmark{position:absolute;left:75px;top:38px;font-family:var(--head);font-weight:700;font-size:38px;line-height:1;color:var(--black);text-transform:uppercase;display:flex;align-items:center;gap:10px}
.wordmark .dot{width:16px;height:16px;border-radius:50%;background:var(--yellow)}
.main-nav{position:absolute;left:279px;top:54px;display:flex;gap:0}
.main-nav a{font-family:var(--head);font-weight:600;font-size:16px;color:var(--ink);text-decoration:none;margin-right:33px}
.main-nav a.active{color:var(--red)}
.social-row{position:absolute;display:flex;gap:14px}
.social-row span{width:17px;height:17px;border-radius:50%;background:currentColor;display:block}

/* hero */
.hero{position:absolute;left:0;top:124px;width:1200px;height:690px;background:
  radial-gradient(ellipse at 72% 40%, #7a3a35 0%, #3a1614 35%, #140808 70%),#0b0505}
.hero-copy{position:absolute;left:75px;top:160px;color:var(--white)}
.hero-title{font-family:var(--head);font-weight:600;font-size:62px;line-height:1}
.hero-sub{font-family:var(--head);font-weight:500;font-size:27px;color:var(--yellow);margin-top:12px}
.hero-text{font-family:var(--head);font-weight:500;font-size:19px;line-height:30px;margin-top:20px;width:460px;text-transform:uppercase}
.btn{display:inline-block;font-family:var(--head);font-weight:500;text-transform:uppercase;border-radius:30px;text-align:center}
.btn-red{background:var(--red);color:var(--white)}
.hero .btn-red{position:absolute;left:75px;top:418px;width:163px;height:51px;line-height:51px;font-size:19px}
.dots{position:absolute;left:75px;top:528px;display:flex;gap:6px}
.dots i{width:12px;height:12px;border-radius:50%;background:var(--white)}
.dots i:first-child{background:var(--yellow)}

.section-title{position:absolute;font-family:var(--head);font-weight:600;font-size:42px;text-transform:uppercase}
.center{width:1200px;text-align:center;left:0}

/* song cards */
.card-img{position:absolute;border-radius:10px}
.card-title{position:absolute;font-family:var(--head);font-weight:500;font-size:23px;text-transform:uppercase}
.card-desc{position:absolute;font-size:15px;color:var(--grey)}
.meta{position:absolute;font-size:15px;font-weight:500;color:var(--red);display:flex;align-items:center;gap:8px}
.btn-yellow{position:absolute;background:var(--yellow);color:var(--black);font-size:13px;height:34px;line-height:34px;width:107px}
.arrow{position:absolute}

/* podcast */
.podcast-bg{position:absolute;left:0;top:1300px;width:1200px;height:677px}
.on-dark{color:var(--white)}
.on-dark .card-desc,.card-desc.light{color:#ddd}
.meta.gold{color:var(--yellow)}

/* about */
.about-title{position:absolute;left:617px;top:2052px;font-family:var(--head);font-weight:500;font-size:42px;text-transform:uppercase}
.about-text{position:absolute;left:617px;top:2117px;width:510px;font-size:15px;line-height:27px;color:#333}
.quote{position:absolute;left:735px;top:2347px;width:395px;font-size:15px;line-height:27px;font-style:italic;color:#333}
.quote-name{position:absolute;left:735px;top:2430px;font-family:var(--head);font-size:15px;color:var(--red);text-transform:uppercase}

/* brand */
.brand-bg{position:absolute;left:0;top:2547px;width:1200px;height:700px}
.product{position:absolute;top:2670px;width:242px;height:347px;background:var(--white);border-radius:8px}
.product .pic{position:absolute;left:18px;top:14px;width:206px;height:200px;border-radius:6px}
.product h3{position:absolute;left:11px;top:224px;font-family:var(--head);font-weight:400;font-size:21px;line-height:27px;color:var(--ink)}
.product .price{position:absolute;left:11px;top:295px;font-family:var(--head);font-weight:500;font-size:21px;color:var(--red)}
.product .btn-yellow{left:88px;top:289px;width:107px}

/* videos */
.video{position:absolute;top:3291px;width:329px;height:222px;border-radius:8px}

/* footer */
.footer-h{position:absolute;font-family:var(--head);font-weight:600;font-size:19px;color:var(--yellow);text-transform:uppercase}
.footer-link{position:absolute;font-size:15px;color:var(--white)}
.footer-text{position:absolute;font-size:15px;line-height:24px;color:var(--white)}
.email-field{position:absolute;left:598px;top:3841px;width:242px;height:48px;border-radius:25px;background:var(--white);font-size:13px;padding:15px 22px;color:#333}
.copyright{position:absolute;left:75px;top:3890px;font-size:12px;line-height:20px;color:#ccc}
</style>
</head>
<body>

<header class="site-header">
  <div class="wordmark"><span class="dot"></span>Stay Golden</div>
  <nav class="main-nav">
    <a class="active">Home</a><a>Brand</a><a>Songs</a><a>Podcast</a><a>Voice Coach</a><a>Band</a><a>Videos</a><a>Contact</a>
  </nav>
  <div class="social-row" style="left:1000px;top:55px;color:#222" aria-label="Social links">
    <span></span><span></span><span style="background:var(--red)"></span><span></span>
  </div>
</header>

<section class="hero" role="img" aria-label="Photo of the singer performing on stage in a cap">
  <div class="hero-copy">
    <h1 class="hero-title">SUNDAY NIGHT RESET</h1>
    <p class="hero-sub">START YOUR WEEK WITH PURPOSE</p>
    <p class="hero-text">Join Lora Venn every Sunday night for a powerful free Huddle session designed to help you set positive intentions, plan your week, and release anything holding you back.</p>
  </div>
  <a class="btn btn-red">Learn More</a>
  <div class="dots"><i></i><i></i><i></i><i></i></div>
</section>
<svg class="abs" style="left:0;top:640px" width="1200" height="180" viewBox="0 0 1200 180">
  <polygon points="0,130 1125,20 1200,20 1200,180 0,180" fill="#fff"/>
  <polygon points="0,128 1125,22 1125,57 0,165" fill="#e8322c"/>
</svg>

<!-- songs -->
<h2 class="section-title center" style="top:842px">Songs</h2>
<svg class="arrow" style="left:22px;top:1116px" width="38" height="30" viewBox="0 0 38 30"><path d="M36 15H5M16 3 4 15l12 12" stroke="#666" stroke-width="5" fill="none"/></svg>
<svg class="arrow" style="left:1140px;top:1116px" width="38" height="30" viewBox="0 0 38 30"><path d="M2 15h31M22 3l12 12-12 12" stroke="#e8322c" stroke-width="5" fill="none"/></svg>

<div class="card-img" style="left:75px;top:927px;width:242px;height:222px;background:linear-gradient(135deg,#8a0f0c,#d2331f)" role="img" aria-label="Single cover, singer in red light"></div>
<div class="card-img" style="left:345px;top:927px;width:242px;height:222px;background:linear-gradient(135deg,#d9d9d9,#555)" role="img" aria-label="Black and white band photo"></div>
<div class="card-img" style="left:615px;top:927px;width:242px;height:222px;background:linear-gradient(135deg,#f2e25a,#9bd3e8 50%,#e35aa0)" role="img" aria-label="Live performance poster with band"></div>
<div class="card-img" style="left:885px;top:927px;width:242px;height:222px;background:linear-gradient(135deg,#2a2a2a,#b9a79a)" role="img" aria-label="Singer performing with microphone"></div>

<h3 class="card-title" style="left:75px;top:1168px">Sedut Perspiciatis</h3>
<h3 class="card-title" style="left:345px;top:1168px">Sedut Perspiciatis</h3>
<h3 class="card-title" style="left:615px;top:1168px">Sedut Perspiciatis</h3>
<h3 class="card-title" style="left:885px;top:1168px">Sedut Perspiciatis</h3>
<p class="card-desc" style="left:75px;top:1206px">Duis mollis, est non commodo</p>
<p class="card-desc" style="left:345px;top:1206px">Duis mollis, est non commodo</p>
<p class="card-desc" style="left:615px;top:1206px">Duis mollis, est non commodo</p>
<p class="card-desc" style="left:885px;top:1206px">Duis mollis, est non commodo</p>
<p class="meta" style="left:75px;top:1244px"><svg width="12" height="12" viewBox="0 0 12 12"><path d="M1 4h3l4-3v10L4 8H1z" fill="#e8322c"/></svg>4:30Mins</p>
<p class="meta" style="left:345px;top:1244px"><svg width="12" height="12" viewBox="0 0 12 12"><path d="M1 4h3l4-3v10L4 8H1z" fill="#e8322c"/></svg>4:30Mins</p>
<p class="meta" style="left:615px;top:1244px"><svg width="12" height="12" viewBox="0 0 12 12"><path d="M1 4h3l4-3v10L4 8H1z" fill="#e8322c"/></svg>4:30Mins</p>
<p class="meta" style="left:885px;top:1244px"><svg width="12" height="12" viewBox="0 0 12 12"><path d="M1 4h3l4-3v10L4 8H1z" fill="#e8322c"/></svg>4:30Mins</p>
<a class="btn btn-yellow" style="left:209px;top:1240px">Listen Now</a>
<a class="btn btn-yellow" style="left:477px;top:1240px">Listen Now</a>
<a class="btn btn-yellow" style="left:748px;top:1240px">Listen Now</a>
<a class="btn btn-yellow" style="left:1017px;top:1240px">Listen Now</a>

<!-- podcast -->
<svg class="abs" style="left:0;top:1315px" width="1200" height="662" viewBox="0 0 1200 662">
  <defs><radialGradient id="podGlow" cx="0.5" cy="0.7" r="0.7"><stop offset="0" stop-color="#4a1838"/><stop offset="1" stop-color="#080608"/></radialGradient></defs>
  <polygon points="0,35 1125,150 1200,152 1200,662 0,662" fill="url(#podGlow)"/>
  <polygon points="0,0 1125,115 1125,150 0,35" fill="#e8322c"/>
</svg>
<div class="on-dark">
  <h2 class="section-title" style="left:75px;top:1494px">Podcast</h2>
  <svg class="arrow" style="left:1038px;top:1508px" width="38" height="30" viewBox="0 0 38 30"><path d="M36 15H5M16 3 4 15l12 12" stroke="#fff" stroke-width="5" fill="none"/></svg>
  <svg class="arrow" style="left:1090px;top:1508px" width="38" height="30" viewBox="0 0 38 30"><path d="M2 15h31M22 3l12 12-12 12" stroke="#ffe01b" stroke-width="5" fill="none"/></svg>
  <div class="card-img" style="left:75px;top:1575px;width:329px;height:226px;background:linear-gradient(135deg,#a08a70,#e8e2d8 55%,#6b5a4c)" role="img" aria-label="Episode art, two hosts holding a graphic shirt"></div>
  <div class="card-img" style="left:436px;top:1575px;width:329px;height:226px;background:linear-gradient(135deg,#c0207a,#f07ab0)" role="img" aria-label="Episode art, host laughing in pink tones"></div>
  <div class="card-img" style="left:798px;top:1575px;width:329px;height:226px;background:linear-gradient(135deg,#ffd400,#2a2a2a 60%,#ffd400)" role="img" aria-label="Season three bonus episode art"></div>
  <h3 class="card-title" style="left:75px;top:1814px">Sedut Perspiciatis</h3>
  <h3 class="card-title" style="left:436px;top:1814px">Sedut Perspiciatis</h3>
  <h3 class="card-title" style="left:798px;top:1814px">Sedut Perspiciatis</h3>
  <p class="card-desc light" style="left:75px;top:1851px">Duis mollis, est non commodo</p>
  <p class="card-desc light" style="left:436px;top:1851px">Duis mollis, est non commodo</p>
  <p class="card-desc light" style="left:798px;top:1851px">Duis mollis, est non commodo</p>
  <p class="meta gold" style="left:75px;top:1888px"><svg width="10" height="14" viewBox="0 0 10 14"><rect x="3" y="0" width="4" height="8" rx="2" fill="#ffe01b"/><path d="M1 6a4 4 0 0 0 8 0M5 10v4" stroke="#ffe01b" stroke-width="1.5" fill="none"/></svg>4:30Mins</p>
  <p class="meta gold" style="left:436px;top:1888px"><svg width="10" height="14" viewBox="0 0 10 14"><rect x="3" y="0" width="4" height="8" rx="2" fill="#ffe01b"/><path d="M1 6a4 4 0 0 0 8 0M5 10v4" stroke="#ffe01b" stroke-width="1.5" fill="none"/></svg>4:30Mins</p>
  <p class="meta gold" style="left:798px;top:1888px"><svg width="10" height="14" viewBox="0 0 10 14"><rect x="3" y="0" width="4" height="8" rx="2" fill="#ffe01b"/><path d="M1 6a4 4 0 0 0 8 0M5 10v4" stroke="#ffe01b" stroke-width="1.5" fill="none"/></svg>4:30Mins</p>
</div>

<!-- about voice coach -->
<div class="card-img" style="left:75px;top:2055px;width:512px;height:411px;background:linear-gradient(135deg,#e6e6e6,#7a5a48 55%,#2a2020)" role="img" aria-label="Portrait of the voice coach in a cap and plaid jacket"></div>
<h2 class="about-title">About Voice Coach</h2>
<p class="about-text">Sed ut perspiciatis unde omnis iste natus error sit voluptatem accusantium doloremque laudantium, totam rem aperiam, eaque ipsa quae ab illo inventore veritatis et quasi architecto beatae vitae dicta sunt explicabo. Nemo enim ipsam voluptatem quia voluptas sit aspernatur aut odit aut fugit.</p>
<a class="btn btn-red" style="position:absolute;left:617px;top:2274px;width:177px;height:51px;line-height:51px;font-size:17px">Learn More</a>
<div class="abs" style="left:617px;top:2362px;width:94px;height:94px;border-radius:50%;background:linear-gradient(135deg,#c98a6a,#5a3428)" role="img" aria-label="Student testimonial portrait"></div>
<p class="quote">“ Sed ut perspiciatis unde omnis iste natus error sit voluptatem &nbsp;accusantium doloremque laudantium, totam rem aperiam, eaque ipsa quae..”</p>
<p class="quote-name">-Name Heading</p>

<!-- brand -->
<svg class="abs" style="left:0;top:2547px" width="1200" height="670" viewBox="0 0 1200 670">
  <polygon points="0,0 1200,0 1200,520 0,620" fill="#000"/>
  <polygon points="0,620 1200,520 1200,557 0,660" fill="#e8322c"/>
</svg>
<h2 class="section-title on-dark" style="left:75px;top:2598px">Brand</h2>
<svg class="arrow" style="left:1038px;top:2610px" width="38" height="30" viewBox="0 0 38 30"><path d="M36 15H5M16 3 4 15l12 12" stroke="#fff" stroke-width="5" fill="none"/></svg>
<svg class="arrow" style="left:1090px;top:2610px" width="38" height="30" viewBox="0 0 38 30"><path d="M2 15h31M22 3l12 12-12 12" stroke="#ffe01b" stroke-width="5" fill="none"/></svg>

<div class="product" style="left:75px"><div class="pic" style="background:radial-gradient(circle,#333 40%,#fff 72%)" role="img" aria-label="Black graphic t-shirt"></div><h3>Stay Golden x Halloween<br>Exclusive Tee</h3><span class="price">$23.00</span><a class="btn btn-yellow">Add to Cart</a></div>
<div class="product" style="left:345px"><div class="pic" style="background:radial-gradient(circle,#222 40%,#fff 72%)" role="img" aria-label="Black crewneck sweatshirt"></div><h3>Stay Golden x Halloween<br>Exclusive Tee</h3><span class="price">$23.00</span><a class="btn btn-yellow">Add to Cart</a></div>
<div class="product" style="left:615px"><div class="pic" style="background:radial-gradient(circle,#d8d8d8 40%,#fff 72%)" role="img" aria-label="Grey graphic hoodie"></div><h3>Stay Golden x Halloween<br>Exclusive Tee</h3><span class="price">$23.00</span><a class="btn btn-yellow">Add to Cart</a></div>
<div class="product" style="left:885px"><div class="pic" style="background:radial-gradient(circle,#e8f51a 40%,#fff 72%)" role="img" aria-label="Neon yellow beanie held in a hand"></div><h3>Stay Golden x Halloween<br>Exclusive Tee</h3><span class="price">$23.00</span><a class="btn btn-yellow">Add to Cart</a></div>

<!-- videos -->
<h2 class="section-title center" style="top:3213px">Videos</h2>
<div class="video" style="left:75px;background:linear-gradient(135deg,#2c3a2a,#6a5a48)" role="img" aria-label="Band video still in a garden set"></div>
<div class="video" style="left:436px;background:linear-gradient(135deg,#1a1a1a,#c8a890)" role="img" aria-label="Video still of the singer on stage"></div>
<div class="video" style="left:798px;background:linear-gradient(135deg,#111,#8a8a8a 60%,#e4e4e4)" role="img" aria-label="Video still of a live street performance"></div>
<svg class="abs" style="left:214px;top:3376px" width="52" height="52" viewBox="0 0 52 52"><circle cx="26" cy="26" r="22" fill="none" stroke="#ffe01b" stroke-width="4"/><path d="M20 15v22l18-11z" fill="#ffe01b"/></svg>
<svg class="abs" style="left:575px;top:3376px" width="52" height="52" viewBox="0 0 52 52"><circle cx="26" cy="26" r="24" fill="#ffe01b"/><circle cx="26" cy="26" r="19" fill="none" stroke="#e8322c" stroke-width="4"/><path d="M20 15v22l18-11z" fill="#e8322c"/></svg>
<svg class="abs" style="left:937px;top:3376px" width="52" height="52" viewBox="0 0 52 52"><circle cx="26" cy="26" r="22" fill="none" stroke="#ffe01b" stroke-width="4"/><path d="M20 15v22l18-11z" fill="#ffe01b"/></svg>
<svg class="arrow" style="left:556px;top:3537px" width="38" height="30" viewBox="0 0 38 30"><path d="M36 15H5M16 3 4 15l12 12" stroke="#666" stroke-width="5" fill="none"/></svg>
<svg class="arrow" style="left:608px;top:3537px" width="38" height="30" viewBox="0 0 38 30"><path d="M2 15h31M22 3l12 12-12 12" stroke="#ffe01b" stroke-width="5" fill="none"/></svg>

<!-- footer -->
<svg class="abs" style="left:0;top:3565px" width="1200" height="435" viewBox="0 0 1200 435">
  <polygon points="0,155 1200,48 1200,435 0,435" fill="#000"/>
  <polygon points="0,120 1200,0 1200,48 0,155" fill="#e8322c"/>
</svg>
<footer>
  <div class="wordmark" style="top:3790px;color:#fff"><span class="dot"></span>Stay Golden</div>
  <p class="copyright">Copyright 2024 © Company Name<br>All Right Reserved</p>
  <h4 class="footer-h" style="left:352px;top:3736px">Quick Links</h4>
  <span class="footer-link" style="left:352px;top:3776px">Brand</span>
  <span class="footer-link" style="left:352px;top:3816px">Songs</span>
  <span class="footer-link" style="left:352px;top:3856px">Podcast</span>
  <span class="footer-link" style="left:352px;top:3896px">Voice Coach</span>
  <span class="footer-link" style="left:473px;top:3784px">Band</span>
  <span class="footer-link" style="left:473px;top:3824px">Videos</span>
  <span class="footer-link" style="left:473px;top:3864px">Contact</span>
  <h4 class="footer-h" style="left:598px;top:3736px">Newsletter</h4>
  <p class="footer-text" style="left:598px;top:3772px;width:260px">Nemo enim ipsam voluptatem quia voluptas sit as.</p>
  <div class="email-field">Enter Email</div>
  <svg class="abs" style="left:803px;top:3856px" width="20" height="20" viewBox="0 0 20 20"><path d="M2 10 18 2l-5 16-3-6z" fill="none" stroke="#e8322c" stroke-width="2"/></svg>
  <h4 class="footer-h" style="left:908px;top:3736px">Social Media</h4>
  <div class="social-row" style="left:908px;top:3782px;color:#fff" aria-label="Social links">
    <span></span><span></span><span style="background:var(--red)"></span><span></span>
  </div>
</footer>

</body>
</html>
```